Packaging sleeve for food containers

I have designed eco-friendly food prep containers that come in packs of 10. The food containers are beige with a clear lid. I need a design for a cardboard sleeve that wraps around the containers as part of the packaging with all of the information on it. I will upload a basic idea of what I am looking for as well as 2 other similar brands for comparison. I have a template with the information I require to be included but I need the final design to be jazzed up to a professional standard. I need help with colours and the design of the sleeve.

Target Market(s)

People who like to meal prep their food in advance and who might also be environmentally conscious. Female and male, somewhat health conscious. Might be looking to lose or maintain weight or just improve nutrition. Organised people. Age range 20-50(ish).

Font styles to use
Serif
Sans Serif

Requirements
Must have
• The information contained in my example sleeve
Nice to have
• Harmonious colours

```html
<!DOCTYPE html>
<html lang="en">
<head>
<meta charset="utf-8">
<title>Fill n Fuel – Meal Prep Container Sleeve</title>
<link rel="stylesheet" href="https://fonts.googleapis.com/css2?family=Quicksand:wght@400;500;700&display=swap">
<style>
  :root {
    --stage: #e6eaf2;
    --paper: #f7f6f1;
    --sky: #dbeaf7;
    --bar: #9db9e3;
    --amber: #f5a623;
    --fold: #5fc8e6;
    --ink: #2b2b2b;
  }
  html, body {
    margin: 0;
    width: 1200px;
    height: 954px;
    overflow: hidden;
    background: var(--stage);
  }
  .sleeve {
    position: absolute;
    left: 474px;
    top: 27px;
    width: 252px;
    height: 900px;
  }
  .sleeve svg { display: block; font-family: "Quicksand", sans-serif; }
  .amber-text { fill: var(--amber); }
  .ink-text { fill: var(--ink); }
  .stroke-amber { fill: none; stroke: var(--amber); }
  .fold-line { stroke: var(--fold); stroke-width: 0.8; }
</style>
</head>
<body>
<div class="sleeve">
  <svg width="252" height="900" viewBox="0 0 252 900" xmlns="http://www.w3.org/2000/svg">
    <!-- sleeve base -->
    <rect class="sleeve-paper" x="0.5" y="0.5" width="251" height="899" fill="var(--paper)" stroke="var(--fold)" stroke-width="0.8"/>

    <!-- sky band -->
    <rect class="sky-band" x="28" y="135" width="146" height="614" fill="var(--sky)"/>
    <rect class="sky-title-band" x="28" y="351" width="223.5" height="67" fill="var(--sky)"/>

    <!-- fold lines -->
    <line class="fold-line" x1="0" y1="187" x2="252" y2="187"/>
    <line class="fold-line" x1="0" y1="480" x2="252" y2="480"/>
    <line class="fold-line" x1="0" y1="667" x2="252" y2="667"/>

    <!-- top flap, printed upside down -->
    <g class="flap-promo" transform="rotate(180 126 93.5)">
      <text class="amber-text" x="127" y="80" font-size="12" font-weight="500" text-anchor="middle">Winner Winner Meal Prep dinner</text>
      <text class="ink-text" x="124" y="93" font-size="8" text-anchor="middle">Tag us @FillnFuel on <tspan>with</tspan></text>
      <text class="ink-text" x="124" y="105" font-size="8" text-anchor="middle">your containers to win monthly prizes</text>
      <text class="ink-text" x="122" y="138" font-size="7.5" text-anchor="middle">Connect with us</text>
      <text class="ink-text" x="122" y="150" font-size="7.5" text-anchor="middle">www.fillnfuel.com.au</text>
      <circle cx="88" cy="158.5" r="3" fill="var(--bar)"/>
      <text class="ink-text" x="126" y="161" font-size="7.5" text-anchor="middle">@FillnFuel</text>
      <circle class="stroke-amber" cx="209" cy="146" r="33" stroke-width="1.2" opacity="0.6"/>
      <text class="amber-text" x="209" y="149" font-size="9" font-weight="700" text-anchor="middle" opacity="0.7">Fill n Fuel</text>
    </g>

    <!-- front panel -->
    <g class="front-panel">
      <circle class="stroke-amber" cx="101" cy="287" r="61" stroke-width="1.6"/>
      <text class="amber-text brand-name" x="101" y="292" font-size="14" font-weight="700" text-anchor="middle" letter-spacing="1.5">Fill n Fuel</text>

      <circle class="stroke-amber pack-count" cx="213" cy="233" r="16" stroke-width="1.2"/>
      <text class="amber-text" x="213" y="231" font-size="9" text-anchor="middle">10</text>
      <text class="amber-text" x="213" y="241" font-size="9" text-anchor="middle">Pack</text>

      <text class="amber-text" x="241" y="386" font-size="13" text-anchor="end" letter-spacing="1">Eco Friendly Wheatstraw</text>
      <text class="amber-text" x="241" y="403" font-size="11" text-anchor="end" letter-spacing="1">3 compartment</text>
      <text class="amber-text" x="241" y="421" font-size="13" text-anchor="end" letter-spacing="1">MEAL PREP CONTAINERS</text>

      <g class="compartment-diagram" stroke="var(--amber)" fill="none" stroke-width="1">
        <rect x="191" y="452" width="47" height="33"/>
        <rect x="194" y="455" width="18" height="27" rx="4"/>
        <rect x="215" y="455" width="20" height="12.5" rx="4"/>
        <rect x="215" y="469.5" width="20" height="12.5" rx="4"/>
      </g>
      <g class="amber-text" font-size="8" text-anchor="middle">
        <text x="203" y="471">2c</text>
        <text x="225" y="464.5">1c</text>
        <text x="225" y="479">1c</text>
      </g>
    </g>

    <!-- features panel -->
    <g class="feature-grid" font-size="4.5" font-weight="700" text-anchor="middle">
      <g class="feature"><circle class="stroke-amber" cx="63" cy="532" r="14" stroke-width="1.3"/><rect x="55" y="527" width="16" height="10" rx="1.5" class="stroke-amber"/><text class="amber-text" x="63" y="552">Microwave Safe</text></g>
      <g class="feature"><circle class="stroke-amber" cx="102" cy="532" r="14" stroke-width="1.3"/><path d="M102 523v18M94 528l16 8M94 536l16-8" class="stroke-amber"/><text class="amber-text" x="102" y="552">Freezer Safe</text></g>
      <g class="feature"><circle class="stroke-amber" cx="142" cy="532" r="14" stroke-width="1.3"/><circle cx="139" cy="535" r="4" class="stroke-amber"/><circle cx="145" cy="535" r="4" class="stroke-amber"/><text class="amber-text" x="142" y="552">Dishwasher Safe</text></g>

      <g class="feature"><circle class="stroke-amber" cx="63" cy="578" r="14" stroke-width="1.3"/><text class="amber-text" x="63" y="577" font-size="6.5">BPA</text><text class="amber-text" x="63" y="584" font-size="6.5">FREE</text><text class="amber-text" x="63" y="598">BPA Free</text></g>
      <g class="feature"><circle class="stroke-amber" cx="102" cy="578" r="14" stroke-width="1.3"/><path d="M102 588v-18M102 576l-4-4M102 580l4-4M102 584l-4-4" class="stroke-amber"/><text class="amber-text" x="102" y="598">Wheatstraw</text></g>
      <g class="feature"><circle class="stroke-amber" cx="142" cy="578" r="14" stroke-width="1.3"/><path d="M142 569c-4 6-6 9-6 12a6 6 0 0 0 12 0c0-3-2-6-6-12z" class="stroke-amber"/><text class="amber-text" x="142" y="598">Leakproof</text></g>

      <g class="feature"><circle class="stroke-amber" cx="63" cy="622" r="14" stroke-width="1.3"/><path d="M53 617h20M53 621h20M53 625h20M53 629h20" class="stroke-amber"/><text class="amber-text" x="63" y="642">Stackable</text></g>
      <g class="feature"><circle class="stroke-amber" cx="102" cy="622" r="14" stroke-width="1.3"/><g class="stroke-amber"><circle cx="96" cy="618" r="2.5"/><circle cx="102" cy="618" r="2.5"/><circle cx="108" cy="618" r="2.5"/><circle cx="96" cy="626" r="2.5"/><circle cx="102" cy="626" r="2.5"/><circle cx="108" cy="626" r="2.5"/></g><text class="amber-text" x="102" y="642">Reusable</text></g>
      <g class="feature"><circle class="stroke-amber" cx="142" cy="622" r="14" stroke-width="1.3"/><path d="M142 614l7 12h-14z" class="stroke-amber"/><text class="amber-text" x="142" y="642">Recycle</text></g>
    </g>

    <!-- back panel -->
    <g class="back-panel">
      <circle class="stroke-amber" cx="97" cy="812" r="36" stroke-width="1.4"/>
      <text class="amber-text" x="97" y="815" font-size="8.5" font-weight="700" text-anchor="middle" letter-spacing="0.8">Fill n Fuel</text>
      <rect class="web-bar" x="0.5" y="867" width="251" height="16" fill="var(--bar)"/>
      <text x="96" y="879" font-size="11" fill="#ffffff" text-anchor="middle" letter-spacing="0.6">www.fillnfuel.com.au</text>
    </g>
  </svg>
</div>
</body>
</html>
```